Hip / Cool Business Card for Custom Accessory Company

I would like to get a 2 sided design for standard size business cards, glossy (2 inches x 3.5 inches). Can be landscape or portrait layout! The design should include our logo (attached). The card should be extremely clear that the company is Tidy Pebble. Should also have our URL clear. Should also use the color scheme seen on our upcoming site, tidypebble.example. The font we use is called "hurry up." Other than that, please go-to-town. We are targeting 15-45 y.o. market, with a skew on the 20-30 crowd. We do custom and stock iPhone cases as well as Cufflinks, Winestoppers; see the website for more.
Updates

Project Deadline Extended
Reason: Extending in case the US July 4th Holiday is keeping people from working!!

Industry/Entity Type

Landscape

Requirements
Must have
• Must be clear that the website is tidypebble.example. Must be clear that custom designs are an option.
Nice to have
• images of our designs. examples of our designs.
Should not have
• hard on the eyes contrasting colors such as orange on black. green on blue. Should not have any fonts that are considered "old" like Times New Roman. But decorative fonts are fine.

```html
<!DOCTYPE html>
<html lang="en">
<head>
<meta charset="utf-8">
<title>Tidy Pebble Business Card</title>
<link rel="stylesheet" href="https://fonts.googleapis.com/css2?family=Lato:wght@400;700;900&display=swap">
<style>
  :root {
    --teal: #1a97a4;
    --teal-bright: #3cb8c4;
    --ink: #1f1f1f;
    --card: #ffffff;
    --backdrop: #e6e4e1;
    --shadow: rgba(0, 0, 0, 0.16);
  }
  * { box-sizing: border-box; margin: 0; padding: 0; }
  html, body {
    width: 1200px;
    height: 913px;
    overflow: hidden;
    background: var(--backdrop);
    font-family: "Lato", sans-serif;
  }
  .stage { position: relative; width: 1200px; height: 913px; }
  .card {
    position: absolute;
    left: 280px;
    width: 640px;
    height: 366px;
    background: var(--card);
    border-radius: 22px;
    box-shadow: 0 6px 18px var(--shadow);
    overflow: hidden;
  }
  .card--front { top: 60px; }
  .card--back { top: 486px; }

  .wordmark {
    display: flex;
    align-items: center;
    gap: 14px;
    white-space: nowrap;
  }
  .wordmark__dot {
    border-radius: 50%;
    background: var(--teal-bright);
    flex: none;
  }
  .wordmark__name {
    font-weight: 900;
    color: var(--ink);
    text-transform: uppercase;
    letter-spacing: 1px;
    line-height: 1;
    white-space: nowrap;
  }

  .card--front .wordmark {
    position: absolute;
    left: 50%;
    top: 96px;
    transform: translateX(-50%);
  }
  .card--front .wordmark__dot { width: 92px; height: 92px; }
  .card--front .wordmark__name { font-size: 40px; }
  .front__url {
    position: absolute;
    left: 0; right: 0;
    top: 218px;
    text-align: center;
    font-weight: 700;
    font-size: 20px;
    color: var(--teal);
  }
  .front__offer {
    position: absolute;
    left: 0; right: 0;
    top: 252px;
    text-align: center;
    font-weight: 400;
    font-size: 14px;
    letter-spacing: 2px;
    text-transform: uppercase;
    color: var(--ink);
  }

  .card--back .wordmark {
    position: absolute;
    right: 40px;
    top: 40px;
    gap: 10px;
  }
  .card--back .wordmark__dot { width: 70px; height: 70px; }
  .card--back .wordmark__name { font-size: 28px; }

  .back__tab {
    position: absolute;
    left: 0;
    top: 150px;
    width: 10px;
    height: 34px;
    background: var(--teal);
  }
  .person {
    position: absolute;
    left: 42px;
    top: 130px;
  }
  .person__name {
    font-weight: 700;
    font-size: 21px;
    color: var(--teal);
  }
  .person__role {
    font-size: 13px;
    color: var(--ink);
    margin-top: 2px;
  }
  .contact {
    position: absolute;
    left: 42px;
    top: 212px;
    font-size: 13.5px;
    color: var(--teal);
    line-height: 1.32;
  }
  .contact__address { margin-bottom: 6px; }
  .contact__list { list-style: none; }
  .contact__item {
    display: flex;
    align-items: center;
    gap: 8px;
  }
  .contact__icon { width: 13px; height: 13px; flex: none; }
  .contact__item--strong { font-weight: 700; }
</style>
</head>
<body>
<main class="stage">

  <section class="card card--front" aria-label="Card front">
    <div class="wordmark">
      <span class="wordmark__dot"></span>
      <span class="wordmark__name">Tidy Pebble</span>
    </div>
    <p class="front__url">tidypebble.example</p>
    <p class="front__offer">Custom &amp; stock designs</p>
  </section>

  <section class="card card--back" aria-label="Card back">
    <div class="wordmark">
      <span class="wordmark__dot"></span>
      <span class="wordmark__name">Tidy Pebble</span>
    </div>

    <span class="back__tab"></span>

    <div class="person">
      <p class="person__name">Jalen Avery</p>
      <p class="person__role">Founder &amp; CEO</p>
    </div>

    <div class="contact">
      <p class="contact__address">Tidy Pebble<br>418 Birchwood Lane Suite 22<br>Fairview, VA 20100</p>
      <ul class="contact__list">
        <li class="contact__item">
          <svg class="contact__icon" viewBox="0 0 16 16" aria-hidden="true"><path fill="#1f1f1f" d="M3.5 1.5l2.5 0 1 3.5-1.6 1.2a8 8 0 0 0 4.4 4.4L11 9l3.5 1v2.5c0 .8-.7 1.5-1.5 1.5A11.5 11.5 0 0 1 2 3c0-.8.7-1.5 1.5-1.5z"/></svg>
          555.010.2000
        </li>
        <li class="contact__item">
          <svg class="contact__icon" viewBox="0 0 16 16" aria-hidden="true"><rect x="4" y="1" width="8" height="14" rx="1.5" fill="#1f1f1f"/><rect x="5.5" y="3" width="5" height="8" fill="#fff"/></svg>
          555.010.7890
        </li>
        <li class="contact__item contact__item--strong">
          <svg class="contact__icon" viewBox="0 0 16 16" aria-hidden="true"><circle cx="8" cy="8" r="8" fill="#1f1f1f"/><rect x="4" y="5" width="8" height="6" fill="#fff"/><path d="M4 5l4 3.2L12 5" stroke="#1f1f1f" stroke-width="1" fill="none"/></svg>
          hello@tidypebble.example
        </li>
        <li class="contact__item contact__item--strong">
          <svg class="contact__icon" viewBox="0 0 16 16" aria-hidden="true"><circle cx="8" cy="8" r="8" fill="#1f1f1f"/><circle cx="8" cy="8" r="5" stroke="#fff" stroke-width="1" fill="none"/><ellipse cx="8" cy="8" rx="2.2" ry="5" stroke="#fff" stroke-width="1" fill="none"/><path d="M3 8h10" stroke="#fff" stroke-width="1"/></svg>
          tidypebble.example
        </li>
      </ul>
    </div>
  </section>

</main>
</body>
</html>
```